Presentation Folder, for Cancer Awareness, VERY COLORFULL AND MODERN

This will be a standard size folder that will hold standard 8 1/2 x 11 papers with a business card slot on the flap, this is a very easy project with very little text and the design for the back page is already done so all you really have to do is make a very nice colorful front cover, you will see my attachments are labeled and I gave you alot of instructions, this should be a very fast easy project
Updates

Reason: there has not been enough quality designs, sorry

Target Market(s)

Our Target Market is Dr's that Deal with Cancer patients

Industry/Entity Type

Healthcare

Font styles to use
Serif

Colors

Designer to choose colors to be used in the design.

Requirements
Must have
• Project must be tasteful and look professional with the ribbons as the main focal point in the center of folder the folder should be a nice gray color to accent the color of the ribbons , the back page needs no design it is the" Sorvane Test" in the attachments I sent
Nice to have
• I would like the ribbons displayed in a row, I included a logo sample layout
• a picture on the front of the folder under the words Hereditary Cancer Screening - Then under that put the words - The Power of Knowledge - then add the picture I labeled Great Picture in the attachments

```html
<!DOCTYPE html>
<html lang="en">
<head>
<meta charset="utf-8">
<title>Hereditary Cancer Screening Folder</title>
<link href="https://fonts.googleapis.com/css2?family=Tinos:wght@400;700&family=Arimo:wght@400;700&family=Carlito:wght@400;700&family=Ubuntu:ital,wght@1,500&display=swap" rel="stylesheet">
<style>
:root{
  --stage:#2b2b2b;
  --paper:#ffffff;
  --pink:#f294a4;
  --pink-soft:#f7b6c2;
  --red:#e43a35;
  --gene:#e2332f;
  --ink:#1a1a1a;
  --stripe:#ececec;
  --lynch:#fbbf3c;
  --pj:#b9cc3a;
  --lf:#27a84a;
  --cowden:#1a9ad8;
  --hdgc:#6a6a62;
  --fold:#e7e7e7;
}
*{box-sizing:border-box;margin:0;padding:0}
html,body{width:1200px;height:1200px;overflow:hidden;background:var(--stage)}
.canvas{position:relative;width:1200px;height:1200px}
.spread{position:absolute;left:238px;width:764px;background:var(--paper);overflow:hidden}
.spread--outside{top:37px;height:539px}
.spread--inside{top:621px;height:541px}

/* back panel */
.brand{position:absolute;font-family:'Arimo',sans-serif;color:var(--red);letter-spacing:4px;font-size:13px}
.back-brand{left:9px;top:10px}
.back-address{position:absolute;left:9px;top:29px;font-family:'Arimo',sans-serif;font-size:4.3px;color:#888;line-height:7px;letter-spacing:.3px}
.menu-title{position:absolute;right:389px;top:11px;text-align:right;white-space:nowrap;font-family:'Ubuntu',sans-serif;font-style:italic;font-weight:500;color:var(--red);font-size:13.5px}
.menu-title sup{font-size:5px}
.back-meta{position:absolute;right:389px;top:36px;text-align:right;white-space:nowrap;font-family:'Arimo',sans-serif;font-size:4.5px;color:#777;letter-spacing:.3px}
.gene-table{position:absolute;left:74px;top:63px;width:228px;font-family:'Arimo',sans-serif;font-size:5.4px}
.row{display:flex;height:11.42px;align-items:center}
.row:nth-child(odd){background:var(--stripe)}
.row .gene{width:72px;padding-left:5px;color:var(--gene);font-weight:700;letter-spacing:.4px}
.row .organ{color:var(--ink)}
.row.head{background:var(--red);color:#fff}
.row.head .gene,.row.head .organ{color:#fff;font-weight:400}
.row.section{color:#fff;padding-left:11px;font-weight:400;letter-spacing:.2px}
.row.sub .gene{padding-left:11px}
.s-lynch{background:var(--lynch)!important}
.s-pj{background:var(--pj)!important}
.s-lf{background:var(--lf)!important}
.s-cowden{background:var(--cowden)!important}
.s-hdgc{background:var(--hdgc)!important}

/* front cover */
.front{position:absolute;left:382px;top:0;width:382px;height:539px;background:linear-gradient(90deg,var(--fold) 0%,#f7f7f7 18%,#fff 40%,#fff 100%)}
.photo{position:absolute;left:40px;top:84px;width:342px;height:282px;background:radial-gradient(ellipse at 55% 60%,#e8c3a8 0%,#d9b59b 30%,#7fa3c9 62%,#f2f2f2 92%)}
.title{position:absolute;left:12px;top:20px;width:360px;text-align:center;font-family:'Tinos',serif;font-weight:700;font-size:26px;color:var(--pink);white-space:nowrap}
.tagline{position:absolute;left:0;top:62px;width:382px;text-align:center;font-family:'Tinos',serif;font-weight:700;font-size:20px;color:var(--ink)}
.cancer-band{position:absolute;left:0;top:366px;width:382px;height:41px;background:var(--pink-soft);font-family:'Carlito',sans-serif;font-weight:700;font-size:9.4px;color:#2a1a1a;text-align:center;padding-top:9px;line-height:11.4px}
.ribbons{position:absolute;left:62px;top:419px;width:254px;height:44px;border-radius:4px;background:linear-gradient(90deg,#f6e43a,#d9d9d9,#7ecbd0,#f28db2,#b044c9,#5b3fd0,#e98a2a,#8a4a22,#f0c8a8,#3aa84a,#2a76d8,#111,#e2e2e2,#f5a0c0,#16a39a,#9b4cd1,#6aa0f0,#e8e8f8)}
.pillars{position:absolute;left:0;top:463px;width:382px;font-family:'Tinos',serif;font-weight:700;font-size:15.5px;color:var(--ink)}
.pillars span{position:absolute;top:0}
.pillars .fast{left:88px}.pillars .comp{left:140px}.pillars .easy{left:269px}
.rule{position:absolute;left:102px;top:487px;width:192px;height:1px;background:linear-gradient(90deg,transparent,#8b9ad4,transparent)}
.front-brand{position:absolute;left:6px;top:506px;display:flex;flex-direction:column;align-items:flex-start;gap:3px}
.front-brand .dot{width:14px;height:14px;border-radius:50%;background:var(--red);margin-left:30px}
.front-brand .name{font-family:'Arimo',sans-serif;font-size:7.5px;color:var(--red);letter-spacing:2.4px}

/* inside */
.inside-fold{position:absolute;left:382px;top:0;width:70px;height:541px;background:linear-gradient(90deg,#ebebeb,#fff)}
.ghost-name{position:absolute;left:0;top:242px;width:764px;text-align:center;font-family:'Arimo',sans-serif;font-size:44px;letter-spacing:20px;color:#ececec;white-space:nowrap}
.pocket-text{position:absolute;left:14px;top:424px;width:340px;font-family:'Carlito',sans-serif;font-size:12px;line-height:14.8px;color:#fff;text-align:justify;text-align-last:center}
.card-slot{position:absolute;left:516px;top:391px;width:132px;height:94px;background:#fbeef1;font-family:'Carlito',sans-serif;font-size:13px;color:#333;text-align:center;padding-top:52px;line-height:15px;clip-path:polygon(10% 0,90% 0,100% 12%,100% 88%,90% 100%,10% 100%,0 88%,0 12%)}
.partner{position:absolute;left:382px;top:500px;width:382px;text-align:center;font-family:'Carlito',sans-serif;color:#fff}
.partner .name{font-size:18px;font-weight:700;display:block;line-height:20px}
.partner .sub{font-size:12px;display:block}
</style>
</head>
<body>
<div class="canvas">

  <section class="spread spread--outside">
    <div class="back-panel">
      <div class="brand back-brand">CORVAIN LABS</div>
      <div class="back-address">220 LINDEN PARK WAY | SUITE B | MARLOW, GA 30000<br>(tel) 555.014.2210 | (fax) 555.014.2211 | care@corvainlabs.example</div>
      <div class="menu-title">SORVANE<sup>™</sup> Test Menu</div>
      <div class="back-meta">CLIA# 00D0000000 | CORVAINLABS.EXAMPLE</div>

      <div class="gene-table">
        <div class="row head"><span class="gene">GENE</span><span class="organ">CANCER-ASSOCIATED ORGAN/SYSTEMS</span></div>
        <div class="row"><span class="gene">APC</span><span class="organ">Colon</span></div>
        <div class="row"><span class="gene">ATM</span><span class="organ">Breast/Pancreatic/Brain</span></div>
        <div class="row"><span class="gene">BARD1</span><span class="organ">Breast/Ovarian</span></div>
        <div class="row"><span class="gene">BMPR1A</span><span class="organ">Colon</span></div>
        <div class="row"><span class="gene">BRCA1</span><span class="organ">Breast/Ovarian/Prostate</span></div>
        <div class="row"><span class="gene">BRCA2</span><span class="organ">Breast/Ovarian/Prostate</span></div>
        <div class="row"><span class="gene">BRIP1</span><span class="organ">Breast/Ovarian</span></div>
        <div class="row"><span class="gene">CDK4</span><span class="organ">Melanoma</span></div>
        <div class="row"><span class="gene">P16 (CDKN2A)</span><span class="organ">Melanoma/Breast/Pancreatic/Squamous</span></div>
        <div class="row"><span class="gene">FANCC</span><span class="organ">Blood</span></div>
        <div class="row"><span class="gene">MEN1</span><span class="organ">Thyroid/Parathyroid</span></div>
        <div class="row"><span class="gene">MET</span><span class="organ">Renal/Hepatic</span></div>
        <div class="row"><span class="gene">MRE11A</span><span class="organ">Ovarian/Breast</span></div>
        <div class="row"><span class="gene">NBN</span><span class="organ">Breast/Ovarian/Prostate/Melanoma</span></div>
        <div class="row"><span class="gene">NF1</span><span class="organ">Blood</span></div>
        <div class="row"><span class="gene">NTRK1</span><span class="organ">Thyroid/Parathyroid</span></div>
        <div class="row"><span class="gene">PALB2</span><span class="organ">Breast/Ovarian/Pancreatic</span></div>
        <div class="row"><span class="gene">PTCH1</span><span class="organ">Melanoma/Brain/Breast/Colon</span></div>
        <div class="row"><span class="gene">RAD50</span><span class="organ">Breast/Ovarian</span></div>
        <div class="row"><span class="gene">RAD51C</span><span class="organ">Ovarian/Breast</span></div>
        <div class="row"><span class="gene">RAD51D</span><span class="organ">Ovarian/Breast</span></div>
        <div class="row"><span class="gene">RET</span><span class="organ">Lung/Thyroid/Parathyroid</span></div>
        <div class="row"><span class="gene">SMAD4</span><span class="organ">Colon/Pancreas</span></div>
        <div class="row section s-lynch">LYNCH SYNDROME GENES</div>
        <div class="row sub"><span class="gene">MLH1</span><span class="organ">Colorectal/Ovarian</span></div>
        <div class="row sub"><span class="gene">MSH2</span><span class="organ">Colorectal/Ovarian</span></div>
        <div class="row sub"><span class="gene">MSH6</span><span class="organ">Colorectal/Ovarian</span></div>
        <div class="row sub"><span class="gene">PMS2</span><span class="organ">Colorectal/Ovarian</span></div>
        <div class="row sub"><span class="gene">EPCAM</span><span class="organ">Colorectal</span></div>
        <div class="row section s-pj">PEUTZ-JEGHERS SYNDROME GENE</div>
        <div class="row sub"><span class="gene">STK11</span><span class="organ">Breast/Ovarian/Melanoma/Colorectal/Lung</span></div>
        <div class="row section s-lf">LI-FRAUMENI SYNDROME GENE</div>
        <div class="row sub"><span class="gene">CHEK2</span><span class="organ">Breast/Ovarian/Prostate</span></div>
        <div class="row sub"><span class="gene">TP53</span><span class="organ">Breast/Bladder/Ovarian/Squamous</span></div>
        <div class="row section s-cowden">COWDEN SYNDROME GENE</div>
        <div class="row sub"><span class="gene">PTEN</span><span class="organ">Endometrium/Breast/Prostate/Lung</span></div>
        <div class="row section s-hdgc">HEREDITARY DIFFUSE GASTRIC CANCER SYNDROME GENE</div>
        <div class="row sub"><span class="gene">CDH1</span><span class="organ">Breast/Gastric/Ovarian/Prostate</span></div>
        <div class="row sub"><span class="gene">VHL</span><span class="organ">Renal</span></div>
      </div>
    </div>

    <div class="front">
      <div class="photo" role="img" aria-label="Photograph of a smiling older couple embracing"></div>
      <h1 class="title">Hereditary Cancer Screening</h1>
      <h2 class="tagline">The Power of Knowledge</h2>
      <div class="cancer-band">Breast Cancer, , Ovarian Cancer, Endometrial Cancer, Gastric Cancer, Colorectal Cancer,<br>Pancreatic Cancer, Melanoma Cancer, Prostate cancer, lung cancer, Colon Cancer</div>
      <div class="ribbons" role="img" aria-label="Row of multicoloured cancer awareness ribbons"></div>
      <div class="pillars"><span class="fast">Fast</span><span class="comp">Comprehensive</span><span class="easy">Easy</span></div>
      <div class="rule"></div>
      <div class="front-brand"><span class="dot"></span><span class="name">CORVAIN LABS</span></div>
    </div>
  </section>

  <section class="spread spread--inside">
    <div class="inside-fold"></div>
    <div class="ghost-name">CORVAIN LABS</div>
    <svg width="764" height="541" style="position:absolute;left:0;top:0" aria-hidden="true">
      <path d="M0 371 H356 Q370 371 372 385 L382 541 H0 Z" fill="#f294a4"/>
      <path d="M764 371 H408 Q394 371 392 385 L382 541 H764 Z" fill="#f294a4"/>
      <path d="M514 401 L527 389 H637 L650 401 V475 L637 487 H527 L514 475 Z" fill="#b97a86" opacity=".45"/>
    </svg>
    <p class="pocket-text">At our state of the art, CLIA certified and COLA accredited facility we perform Next Generation Sequencing (NGS) based screening for mutations known to affect an individual's Risk of developing Hereditary Cancer. Results from the test enable the Physician to make Better informed treatment decisions.</p>
    <div class="card-slot">Space for<br>Business card</div>
    <div class="partner"><span class="name">Orvell Health Partners</span><span class="sub">An independent arm of Corvain Labs LLC</span></div>
  </section>

</div>
</body>
</html>
```